Talon Microsystems PowerPoint Master Slide Deck Design

This is a 2-phase project to design a slide deck for a semiconductor company in the Silicon Valley. The design budget will be increased with each phase.
The slide deck will need to have one version with a dark background for presentations and a second version with a white background. Otherwise, the slides will be the same. I anticipate we will need a total of 10 slides, but that number may change.
The first phase will be to design a Title and a Title and Content slide.
- The Title Slide is the first slide of the deck. It should include the presentation title, the presenter's name and date of presentation
- The Title and Content slide should include a title and content with bullet points and up to 2 additional sub-bullets
- The Title and Content slide should have a footer that includes the slide #, Talon Microsystems Confidential, and the logo. This footer will be on every slide except the Title Slide
The first two slides will serve as the format for the remaining ~8 slides:
-Header and Content Text (1, 2, 4 column)
-Header and Content Image (bar chart, pie chart, tables)
-Break
-Title only
-Closing (Talon logo only)
Our slides contain a lot of content so a clean and simple design is best.
Both phases will need to include pre-set color options for
-Text and Lines
-Shadows
-Bullets and sub-bullets (including shapes, ex. circle, slash, square, etc.)
-Bar charts, pie charts, tables
Samples of our collateral are attached. Logo files are also attached
Look and feel
Each slider illustrates characteristics of the customer's brand and the style your logo design should communicate.

```html
<!DOCTYPE html>
<html lang="en">
<head>
<meta charset="utf-8">
<title>Talon Microsystems Slide Deck</title>
<link href="https://fonts.googleapis.com/css2?family=Poppins:wght@400;500;600&display=swap" rel="stylesheet">
<style>
  :root {
    --page: #ffffff;
    --slide: #000000;
    --brand: #0a52b3;
    --brand-light: #1772c9;
    --brand-bright: #1f7fe0;
    --panel: #3a3a3a;
    --text: #ffffff;
    --grid: #6a6a6a;
  }
  * { box-sizing: border-box; margin: 0; padding: 0; }
  html, body { width: 1200px; height: 4057px; overflow: hidden; }
  body { background: var(--page); position: relative; font-family: "Poppins", sans-serif; color: var(--text); }

  .slide { position: absolute; left: 51px; width: 1088px; height: 612px; background: var(--slide); overflow: hidden; }
  .slide > * { position: absolute; }

  .heading { font-size: 21px; font-weight: 600; color: var(--brand-light); text-transform: uppercase; letter-spacing: .3px; }
  .heading .lead { font-weight: 500; border-bottom: 2px solid var(--brand-light); }

  .body-copy { font-size: 10.5px; line-height: 25px; color: var(--text); }

  /* footer */
  .footer { left: 0; top: 545px; width: 1088px; height: 50px; }
  .footer .tab { position: absolute; left: 0; top: 0; width: 47px; height: 50px; background: var(--brand); }
  .footer .brand { position: absolute; left: 68px; top: 0; height: 50px; display: flex; align-items: center; gap: 10px; font-size: 25px; font-weight: 500; color: var(--text); }
  .footer .brand .dot { width: 14px; height: 14px; border-radius: 50%; background: var(--brand-bright); }
  .footer .band { position: absolute; left: 254px; top: 0; width: 834px; height: 50px; background: var(--brand); font-size: 15px; font-weight: 500; text-transform: uppercase; }
  .footer .band .label { position: absolute; left: 211px; top: 14px; }
  .footer .band .page { position: absolute; left: 689px; top: 14px; word-spacing: 20px; }

  /* title slide */
  .title-photo { left: 0; top: 0; width: 1088px; height: 612px;
    background: radial-gradient(ellipse at 68% 38%, #3fd2ff 0%, #1073d9 18%, #0b2f8a 48%, #071b4f 100%); }
  .title-main { left: 27px; top: 440px; font-size: 30px; font-weight: 500; text-transform: uppercase; }
  .title-sub { left: 27px; top: 494px; font-size: 22px; font-weight: 500; }
  .title-date { left: 27px; top: 545px; font-size: 22px; font-weight: 500; }

  /* about */
  .about-box { left: 22px; top: 143px; width: 352px; height: 365px; background: var(--brand); padding: 24px 26px; }
  .about-col { top: 167px; width: 310px; }

  /* services */
  .services-photo { left: 31px; top: 48px; width: 447px; height: 446px; border-radius: 14px;
    background: radial-gradient(circle at 45% 55%, #7fd3ff 0%, #1f7fe0 30%, #0a3a8f 70%, #061a45 100%); }
  .service { top: 355px; width: 120px; text-align: center; }
  .service .icon { width: 62px; height: 63px; margin: 0 auto; background: var(--brand); border-radius: 4px; display: flex; align-items: center; justify-content: center; }
  .service .name { margin-top: 18px; font-size: 13px; color: var(--brand-light); }

  /* graph */
  .chart { left: 0; top: 0; }
  .note { width: 338px; height: 172px; background: var(--panel); padding: 20px 20px 0 42px; font-size: 10.5px; line-height: 25px; }
  .note-mark { width: 33px; height: 33px; background: var(--brand-light); }

  /* specialization */
  .spec-col { top: 104px; width: 470px; }
  .spec-lead { position: relative; padding-left: 25px; width: 400px; font-size: 10.5px; line-height: 25px; color: var(--brand-light); font-weight: 500; }
  .spec-lead::before { content: ""; position: absolute; left: 0; top: 8px; width: 9px; height: 9px; border-radius: 50%; border: 2px solid var(--brand-light); background: radial-gradient(circle, var(--brand-light) 35%, transparent 40%); }
  .spec-list { list-style: none; margin-top: 12px; }
  .spec-list li { position: relative; padding-left: 42px; width: 412px; font-size: 10.5px; line-height: 25px; margin-bottom: 13px; }
  .spec-list li::before { content: "»"; position: absolute; left: 25px; top: 0; font-weight: 600; }

  /* closing */
  .closing-photo { left: 0; top: 0; width: 1088px; height: 612px;
    background: radial-gradient(ellipse at 50% 50%, #15191f 0%, #0d1015 60%, #07090c 100%); }
  .closing-brand { left: 0; top: 0; width: 1088px; height: 612px; display: flex; align-items: center; justify-content: center; gap: 26px; font-size: 64px; font-weight: 500; }
  .closing-brand .dot { width: 44px; height: 44px; border-radius: 50%; background: var(--brand-bright); }
</style>
</head>
<body>

<!-- Title -->
<section class="slide" style="top:51px">
  <div class="title-photo" role="img" aria-label="Glowing blue microchip on a circuit board"></div>
  <h1 class="title-main">Talon Microsystems</h1>
  <p class="title-sub">LOREM IPSUM</p>
  <p class="title-date">13-12-2023</p>
</section>

<!-- About -->
<section class="slide" style="top:715px">
  <h2 class="heading" style="left:58px;top:57px"><span class="lead">About</span> Talon Microsystems</h2>
  <div class="about-box body-copy">Sed ut perspiciatis unde omnis iste natus error sit voluptatem accusantium doloremque laudantium, totam rem aperiam, eaque ipsa quae ab illo inventore veritatis et quasi architecto beatae vitae dicta sunt explicabo. Nemo enim ipsam voluptatem quia voluptas sit aspernatur aut odit aut fugit, sed quia consequuntur magni dolores eos qui ratione voluptatem sequi nesciunt. Neque porro quisquam est, qui dolorem Excepteur sint occaecat cupidatat non proident, sunt in culpa qui officia deserunt mollit anim id est laborum. sed quia non numquam eius modi tempora incidunt ut labore et dolore magnam aliquam quaerat voluptatem.</div>
  <p class="about-col body-copy" style="left:421px">Sed ut perspiciatis unde omnis iste natus error sit voluptatem accusantium doloremque laudantium, totam rem aperiam, eaque ipsa quae ab illo inventore veritatis et quasi architecto beatae vitae dicta sunt explicabo. Nemo enim ipsam voluptatem quia voluptas sit aspernatur aut odit aut fugit, sed quia consequuntur magni dolores eos qui ratione voluptatem sequi nesciunt. Neque porro quisquam est, qui dolorem Excepteur sint occaecat cupidatat non proident, sunt in culpa qui officia deserunt mollit anim id est laborum. sed quia non numquam eius modi tempora incidunt ut labore et dolore magnam aliquam quaerat voluptatem.</p>
  <p class="about-col body-copy" style="left:760px">Sed ut perspiciatis unde omnis iste natus error sit voluptatem accusantium doloremque laudantium, totam rem aperiam, eaque ipsa quae ab illo inventore veritatis et quasi architecto beatae vitae dicta sunt explicabo. Nemo enim ipsam voluptatem quia voluptas sit aspernatur aut odit aut fugit, sed quia consequuntur magni dolores eos qui ratione voluptatem sequi nesciunt. Neque porro quisquam est, qui dolorem Excepteur sint occaecat cupidatat non proident, sunt in culpa qui officia deserunt mollit anim id est laborum. sed quia non numquam eius modi tempora incidunt ut labore et dolore magnam aliquam quaerat voluptatem.</p>
  <footer class="footer"><div class="tab"></div><div class="brand"><span class="dot"></span>TALON</div><div class="band"><span class="label">Talon Microsystems Confidential</span><span class="page">PAGE | 02</span></div></footer>
</section>

<!-- Services -->
<section class="slide" style="top:1380px">
  <div class="services-photo" role="img" aria-label="Blue processor chip among circuit traces"></div>
  <h2 class="heading" style="left:530px;top:64px">Our Services</h2>
  <p class="body-copy" style="left:530px;top:120px;width:520px">Lorem ipsum dolor sit amet, consectetur adipiscing elit, sed do eiusmod tempor incididunt ut labore et dolore magna aliqua. Ut enim ad minim veniam, quis nostrud exercitation ullamco laboris nisi ut aliquip ex ea commodo consequat. Duis aute irure dolor in reprehenderit in voluptate velit esse cillum dolore eu fugiat nulla pariatur. Excepteur sint occaecat cupidatat non proident, sunt in culpa qui officia deserunt mollit anim id est laborum. Sed ut perspiciatis unde omnis iste natus error sit voluptatem accusantium doloremque laudantium, totam rem aperiam, eaque ipsa quae ab illo inventore veritatis et quasi architecto beatae vitae dicta sunt explicabo. Nemo enim ipsam voluptatem quia voluptas sit aspernatur aut odit aut fugit</p>
  <div class="service" style="left:512px"><div class="icon"><svg width="40" height="40" viewBox="0 0 40 40" fill="none" stroke="#fff" stroke-width="1.6"><rect x="9" y="9" width="22" height="22"/><rect x="14" y="14" width="12" height="12"/><path d="M13 4v5M20 4v5M27 4v5M13 31v5M20 31v5M27 31v5M4 13h5M4 20h5M4 27h5M31 13h5M31 20h5M31 27h5"/></svg></div><p class="name">LOREM IPSUM</p></div>
  <div class="service" style="left:652px"><div class="icon"><svg width="40" height="40" viewBox="0 0 40 40" fill="none" stroke="#fff" stroke-width="1.6"><rect x="9" y="9" width="22" height="22" rx="2"/><path d="M14 16h12M14 20h8M14 24h10M13 4v5M20 4v5M27 4v5M13 31v5M20 31v5M27 31v5M4 13h5M4 20h5M4 27h5M31 13h5M31 20h5M31 27h5"/></svg></div><p class="name">LOREM IPSUM</p></div>
  <div class="service" style="left:794px"><div class="icon"><svg width="40" height="40" viewBox="0 0 40 40" fill="none" stroke="#fff" stroke-width="1.6"><rect x="14" y="14" width="12" height="12"/><path d="M20 14V5M20 26v9M14 20H5M26 20h9M16 14l-6-6M24 14l6-6M16 26l-6 6M24 26l6 6"/><circle cx="20" cy="4" r="2"/><circle cx="4" cy="20" r="2"/><circle cx="36" cy="20" r="2"/><circle cx="20" cy="36" r="2"/></svg></div><p class="name">LOREM IPSUM</p></div>
  <div class="service" style="left:936px"><div class="icon"><svg width="40" height="40" viewBox="0 0 40 40" fill="none" stroke="#fff" stroke-width="1.6"><circle cx="20" cy="20" r="11"/><circle cx="20" cy="20" r="5"/><path d="M20 4v5M20 31v5M4 20h5M31 20h5M9 9l3.5 3.5M27.5 27.5L31 31M31 9l-3.5 3.5M12.5 27.5L9 31"/></svg></div><p class="name">LOREM IPSUM</p></div>
  <footer class="footer"><div class="tab"></div><div class="brand"><span class="dot"></span>TALON</div><div class="band"><span class="label">Talon Microsystems Confidential</span><span class="page">PAGE | 03</span></div></footer>
</section>

<!-- Graph -->
<section class="slide" style="top:2044px">
  <h2 class="heading" style="left:48px;top:48px">Our Graph</h2>
  <svg class="chart" width="680" height="530" viewBox="0 0 680 530" font-family="Poppins, sans-serif" font-size="14" fill="#fff">
    <g stroke="#6a6a6a" stroke-width="1">
      <line x1="86" y1="161" x2="631" y2="161"/><line x1="86" y1="212" x2="631" y2="212"/><line x1="86" y1="263" x2="631" y2="263"/><line x1="86" y1="314" x2="631" y2="314"/><line x1="86" y1="365" x2="631" y2="365"/><line x1="86" y1="416" x2="631" y2="416"/><line x1="86" y1="467" x2="631" y2="467"/>
    </g>
    <g text-anchor="middle">
      <text x="67" y="166">6</text><text x="67" y="217">5</text><text x="67" y="268">4</text><text x="67" y="319">3</text><text x="67" y="370">2</text><text x="67" y="421">1</text><text x="67" y="472">0</text>
    </g>
    <g fill="#0a52b3">
      <rect x="132" y="314" width="14" height="153"/><rect x="260" y="257" width="14" height="210"/><rect x="391" y="365" width="14" height="102"/><rect x="531" y="237" width="14" height="230"/>
    </g>
    <g fill="#1772c9">
      <rect x="157" y="288" width="14" height="179"/><rect x="284" y="216" width="14" height="251"/><rect x="414" y="340" width="14" height="127"/><rect x="556" y="191" width="14" height="276"/>
    </g>
    <g text-anchor="middle" font-size="13" font-weight="500">
      <text x="151" y="503">CATEGORY 1</text><text x="279" y="503">CATEGORY 2</text><text x="410" y="503">CATEGORY 3</text><text x="551" y="503">CATEGORY 4</text>
    </g>
  </svg>
  <div class="note" style="left:707px;top:79px">Lorem ipsum dolor sit amet, consectetur adipiscing elit, sed do eiusmod tempor incididunt ut labore et dolore magna aliqua. Ut enim ad minim veniam, quis nostrud exercitation ullamco laboris nisi ut aliquip ex ea commodo consequat. Duis aute irure</div>
  <div class="note-mark" style="left:693px;top:150px"></div>
  <div class="note" style="left:707px;top:288px">Lorem ipsum dolor sit amet, consectetur adipiscing elit, sed do eiusmod tempor incididunt ut labore et dolore magna aliqua. Ut enim ad minim veniam, quis nostrud exercitation ullamco laboris nisi ut aliquip ex ea commodo consequat. Duis aute irure</div>
  <div class="note-mark" style="left:693px;top:357px"></div>
  <footer class="footer"><div class="tab"></div><div class="brand"><span class="dot"></span>TALON</div><div class="band"><span class="label">Talon Microsystems Confidential</span><span class="page">PAGE | 04</span></div></footer>
</section>

<!-- Specialization -->
<section class="slide" style="top:2709px">
  <h2 class="heading" style="left:81px;top:47px">Our Specialization</h2>
  <div class="spec-col" style="left:87px">
    <p class="spec-lead">Lorem ipsum dolor sit amet, consectetur adipiscing elit, sed do eiusmod tempor incididunt ut labore et dolore magna aliqua.</p>
    <ul class="spec-list">
      <li>Sed ut perspiciatis unde omnis iste natus error sit voluptatem accusantium doloremque laudantium, totam rem aperiam, eaque ipsa quae ab illo inventore veritatis et quasi architecto beatae vitae dicta sunt explicabo.</li>
      <li>Sed ut perspiciatis unde omnis iste natus error sit voluptatem accusantium doloremque laudantium, totam rem aperiam, eaque ipsa quae ab illo inventore veritatis et quasi architecto beatae vitae dicta sunt explicabo.</li>
      <li>Sed ut perspiciatis unde omnis iste natus error sit voluptatem accusantium doloremque laudantium, totam rem aperiam, eaque ipsa quae ab illo inventore veritatis et quasi architecto beatae vitae dicta sunt explicabo.</li>
    </ul>
  </div>
  <div class="spec-col" style="left:584px">
    <p class="spec-lead">Lorem ipsum dolor sit amet, consectetur adipiscing elit, sed do eiusmod tempor incididunt ut labore et dolore magna aliqua.</p>
    <ul class="spec-list">
      <li>Sed ut perspiciatis unde omnis iste natus error sit voluptatem accusantium doloremque laudantium, totam rem aperiam, eaque ipsa quae ab illo inventore veritatis et quasi architecto beatae vitae dicta sunt explicabo.</li>
      <li>Sed ut perspiciatis unde omnis iste natus error sit voluptatem accusantium doloremque laudantium, totam rem aperiam, eaque ipsa quae ab illo inventore veritatis et quasi architecto beatae vitae dicta sunt explicabo.</li>
      <li>Sed ut perspiciatis unde omnis iste natus error sit voluptatem accusantium doloremque laudantium, totam rem aperiam, eaque ipsa quae ab illo inventore veritatis et quasi architecto beatae vitae dicta sunt explicabo.</li>
    </ul>
  </div>
  <footer class="footer"><div class="tab"></div><div class="brand"><span class="dot"></span>TALON</div><div class="band"><span class="label">Talon Microsystems Confidential</span><span class="page">PAGE | 05</span></div></footer>
</section>

<!-- Closing -->
<section class="slide" style="top:3373px">
  <div class="closing-photo" role="img" aria-label="Dark circuit board background"></div>
  <div class="closing-brand"><span class="dot"></span>Talon Microsystems</div>
</section>

</body>
</html>
```